Cutting Edge Property Services Provider is Looking to Update Business Card Design

We are looking to freshen up our business cards to match our cutting edge technology based image.

KORVANEX - Where Care Finds Its Pulse

More information about our company can be found on our website at www.korvanex-demo.net

We integrate technology in a historically low tech industry.

We have appeared on the Brisk 300/3000 list 2 years in a row and we're previously recognized as the 5th Quickest Rising Firm in San Diego.

Our core colors are blue and white, but are not against accents that might improve our image.

We currently have our Mission Statement on our Business Cards in a folding design:
KORVANEX IS THE LEADING BUILDING SERVICES INNOVATOR. BY COMBINING TECHNOLOGY WITH FUNCTIONAL TOOS THAT IMPROVE EFFICIENCY IN THE WORKPLACE, WE PROVIDE UNPARALLELED SERVICE IN THE INDUSTRY. DEVELOPING LASTING RELATIONSHIPS WITH OUR CLIENTS AND ASSOCIATES IS THE CORNERSTONE OF OUR SUCCESS.

We'd like to convey the image of a cutting edge, technology based company. Want the cards to pop.

Target Market(s)

Commercial Property Managers - 20 to 50 year old professionals

Industry/Entity Type

Business

Requirements
Must have
• Must utilize our logo obviously, but are definitely open to using variations on the logo. Utilizing the components of the logo, but maybe in different configurations or backgrounds, etc...

Must use the Name: KORVANEX.
Can also use KORVANEX PROPERTY SERVICES.

Must include the Mission Statement

Must say: Where Care Finds Its Pulse
Nice to have
• We are considering plastic stock, shaped cards, or folding cards.

Nothing over the top or really expensive, but will consider if it conveys innovation and technology.
Should not have
• No images of toilets, buildings, trees, or anything relating to commercial properties.

We want to convey our technology image.

```html
<!DOCTYPE html>
<html lang="en">
<head>
<meta charset="utf-8">
<title>KORVANEX Business Cards</title>
<link rel="stylesheet" href="https://fonts.googleapis.com/css2?family=Open+Sans:wght@300;400;700;800&display=swap">
<style>
  :root {
    --brand-blue: #0b4a7e;
    --brand-blue-soft: #1d5a8c;
    --card-white: #ffffff;
    --rule-grey: #b9bec4;
    --ink-grey: #3b3f44;
    --backdrop: #b67a48;
  }
  * { margin: 0; padding: 0; box-sizing: border-box; }
  html, body { width: 1200px; height: 691px; overflow: hidden; }
  body {
    position: relative;
    background: var(--backdrop);
    font-family: "Open Sans", Arial, sans-serif;
  }
  .card {
    position: absolute;
    width: 541px;
    height: 307px;
    border-radius: 30px;
    overflow: hidden;
  }
  .card--front { left: 320px; top: 21px; background: var(--card-white); border: 1px solid #2a2a2a; }
  .card--back-blue { left: 45px; top: 351px; background: var(--brand-blue); }
  .card--back-white { left: 626px; top: 351px; background: var(--card-white); }

  .brand {
    position: absolute;
    left: 0; right: 0; top: 62px;
    display: flex; align-items: center; justify-content: center; gap: 14px;
  }
  .brand__mark { width: 40px; height: 40px; background: var(--brand-blue); border-radius: 4px; }
  .brand__name {
    font-weight: 800; font-size: 44px; letter-spacing: 2px;
    color: var(--brand-blue); line-height: 1;
  }

  .rule { position: absolute; left: 0; right: 0; height: 2px; background: var(--rule-grey); }
  .rule--top { top: 180px; }
  .rule--bottom { top: 222px; }
  .tagline-band {
    position: absolute; left: 0; right: 0; top: 186px; height: 31px;
    background: var(--brand-blue);
    color: var(--card-white);
    font-weight: 400; font-size: 17px; letter-spacing: 1.2px;
    display: flex; align-items: center; justify-content: center;
  }

  .address {
    position: absolute; right: 283px; top: 234px;
    text-align: right; font-weight: 300; font-size: 15px; line-height: 20px;
    color: var(--ink-grey);
  }
  .divider { position: absolute; left: 268px; top: 236px; width: 1px; height: 60px; background: var(--rule-grey); }
  .contact {
    position: absolute; left: 278px; top: 234px;
    font-weight: 300; font-size: 15px; line-height: 20px; color: var(--ink-grey);
    list-style: none;
  }
  .contact li { display: flex; align-items: center; gap: 5px; }
  .contact svg { width: 11px; height: 11px; fill: var(--ink-grey); flex: none; }

  .mission {
    position: absolute; left: 0; right: 0; top: 52px;
    text-align: center; font-weight: 400; font-size: 16.5px; line-height: 30.3px;
  }
  .card--back-blue .mission { color: var(--card-white); }
  .card--back-white .mission { color: var(--brand-blue); }
</style>
</head>
<body>

<section class="card card--front">
  <div class="brand">
    <span class="brand__mark"></span>
    <span class="brand__name">KORVANEX</span>
  </div>
  <div class="rule rule--top"></div>
  <div class="tagline-band">Where Care Finds Its Pulse</div>
  <div class="rule rule--bottom"></div>
  <address class="address">
    2814 Meridian Crest Blvd.<br>
    Suite 210<br>
    San Diego, CA 92108
  </address>
  <div class="divider"></div>
  <ul class="contact">
    <li>
      <svg viewBox="0 0 12 12" aria-hidden="true"><path d="M2.5 1 4.5 3.3 3.5 4.6c.7 1.6 2 2.9 3.6 3.6l1.3-1 2.3 2-1 1.6C5.3 11 1 6.7.8 2z"/></svg>
      1(866) 555-0142
    </li>
    <li>
      <svg viewBox="0 0 12 12" aria-hidden="true"><path d="M1 3h10v7H1z M1.5 3.5 6 7l4.5-3.5" fill="none" stroke="#3b3f44" stroke-width="1.2"/></svg>
      info@korvanex-demo.net
    </li>
    <li>
      <svg viewBox="0 0 12 12" aria-hidden="true"><circle cx="6" cy="6" r="5"/><path d="M1 6h10M6 1c-2.5 3-2.5 7 0 10M6 1c2.5 3 2.5 7 0 10" stroke="#fff" stroke-width=".8" fill="none"/></svg>
      www.korvanex-demo.net
    </li>
  </ul>
</section>

<section class="card card--back-blue">
  <p class="mission">
    KORVANEX IS THE LEADING BUILDING SERVICES INNOVATOR.<br>
    BY COMBINING TECHNOLOGY WITH FUNCTIONAL TOOS THAT<br>
    IMPROVE EFFICIENCY IN THE WORKPLACE, WE PROVIDE<br>
    UNPARALLELED SERVICE IN THE INDUSTRY. DEVELOPING<br>
    LASTING RELATIONSHIPS WITH OUR CLIENTS AND ASSOCIATES<br>
    IS THE CORNERSTONE OF OUR SUCCESS.
  </p>
</section>

<section class="card card--back-white">
  <p class="mission">
    KORVANEX IS THE LEADING BUILDING SERVICES INNOVATOR.<br>
    BY COMBINING TECHNOLOGY WITH FUNCTIONAL TOOS THAT<br>
    IMPROVE EFFICIENCY IN THE WORKPLACE, WE PROVIDE<br>
    UNPARALLELED SERVICE IN THE INDUSTRY. DEVELOPING<br>
    LASTING RELATIONSHIPS WITH OUR CLIENTS AND ASSOCIATES<br>
    IS THE CORNERSTONE OF OUR SUCCESS.
  </p>
</section>

</body>
</html>
```